Business Card Design - Property Management & Real Estate Services

I need a business card design for my company that I can print ZEPLA Cards. The company is called Brindle Management Company. It is a property management and real estate company. The design has to be clean and modern. I need two versions. One for my employee and one for me. However, the design will be the same, just different text. You can get a feel for the company by looking at our website at www.brindlemanagement.example.

Industry/Entity Type

Property Management

Contact Information for Business Card

I will be using ZEPLA.com to print my cards. I will most likely use the rounded edges card. I need two versions, however, they will be the same design. I need one for me and my employee.

Colors
3276b5
33a6d7

Requirements
Must have
• Company Logo
• Name of person
• Property Management & Real Estate Service
• Phone
• Email
• Website
• Address
• A space to place a QR code

```html
<!DOCTYPE html>
<html lang="en">
<head>
<meta charset="utf-8">
<title>Brindle Management – Business Cards</title>
<link href="https://fonts.googleapis.com/css2?family=Exo+2:wght@600&family=Montserrat:wght@500&family=Roboto:wght@400&display=swap" rel="stylesheet">
<style>
  :root{
    --bg:#c9c9c9;
    --card:#ffffff;
    --brand-dark:#1f54a6;
    --brand-light:#5b93d3;
    --ink:#2b2b2b;
  }
  *{box-sizing:border-box;margin:0;padding:0}
  html,body{width:1200px;height:852px;overflow:hidden}
  body{background:var(--bg);font-family:"Roboto",sans-serif;position:relative}
  .card{
    position:absolute;width:525px;height:300px;background:var(--card);
    border-radius:18px;overflow:hidden;box-shadow:0 4px 10px rgba(0,0,0,.18);
  }
  .card--front{left:45px;top:276px}
  .card--back{left:630px;top:276px}

  .wordmark{font-family:"Montserrat",sans-serif;font-weight:500;color:var(--brand-dark);line-height:1}
  .wordmark__name{display:block;letter-spacing:2px}
  .wordmark__tag{display:block;letter-spacing:9px}

  .card--front .wordmark{position:absolute;top:80px;left:0;width:100%;text-align:center}
  .card--front .wordmark__name{font-size:58px}
  .card--front .wordmark__tag{font-size:14px;margin-top:8px;padding-left:9px}
  .front-site{
    position:absolute;top:196px;left:0;width:100%;
    display:flex;justify-content:center;align-items:center;gap:14px;
    font-size:14px;color:var(--ink);
  }
  .front-site::before,.front-site::after{content:"";width:36px;height:2px;background:var(--brand-light)}
  .front-band{position:absolute;left:0;bottom:0;width:100%;height:12px;display:flex}
  .front-band__light{flex:0 0 52%;background:var(--brand-light)}
  .front-band__dark{flex:1;background:var(--brand-dark)}

  .card--back .wordmark{position:absolute;top:34px;left:34px}
  .card--back .wordmark__name{font-size:46px}
  .card--back .wordmark__tag{font-size:11px;margin-top:6px;letter-spacing:7.5px}
  .holder{position:absolute;top:130px;left:34px}
  .holder__name{font-family:"Exo 2",sans-serif;font-weight:600;font-size:20px;color:var(--brand-dark)}
  .holder__role{font-size:14px;color:var(--ink);margin-top:2px}
  .contacts{position:absolute;top:186px;left:34px;list-style:none;font-size:14px;color:var(--ink)}
  .contacts li{display:flex;align-items:center;gap:10px;height:20px}
  .contacts svg{width:13px;height:13px;fill:var(--brand-dark);flex:none}
  .contacts .no-icon{padding-left:23px}
  .back-rule{position:absolute;left:0;bottom:22px;width:100%;height:5px;background:var(--brand-light)}
</style>
</head>
<body>
  <section class="card card--front" aria-label="Card front">
    <div class="wordmark">
      <span class="wordmark__name">BRINDLE</span>
      <span class="wordmark__tag">MANAGEMENT</span>
    </div>
    <p class="front-site">www.brindlemanagement.example</p>
    <div class="front-band"><span class="front-band__light"></span><span class="front-band__dark"></span></div>
  </section>

  <section class="card card--back" aria-label="Card back">
    <div class="wordmark">
      <span class="wordmark__name">BRINDLE</span>
      <span class="wordmark__tag">MANAGEMENT</span>
    </div>
    <div class="holder">
      <p class="holder__name">Mateo R. Salgado</p>
      <p class="holder__role">Founder</p>
    </div>
    <ul class="contacts">
      <li><svg viewBox="0 0 16 16" aria-hidden="true"><path d="M3 1h3l1.5 4-2 1.3a9 9 0 0 0 4.2 4.2L11 8.5l4 1.5v3a2 2 0 0 1-2 2A12 12 0 0 1 1 3a2 2 0 0 1 2-2z"/></svg>(555) 014-2287</li>
      <li><svg viewBox="0 0 16 16" aria-hidden="true"><path d="M1 3h14v10H1zM2 4.2V12h12V4.2L8 9z"/></svg>mateo@brindlemanagement.example</li>
      <li><svg viewBox="0 0 16 16" aria-hidden="true"><path d="M8 1a7 7 0 1 0 0 14A7 7 0 0 0 8 1zm-1 2.2V7H3.1A5 5 0 0 1 7 3.2zm2 0A5 5 0 0 1 12.9 7H9zM3.1 9H7v3.8A5 5 0 0 1 3.1 9zM9 9h3.9A5 5 0 0 1 9 12.8z"/></svg>www.brindlemanagement.example</li>
      <li class="no-icon">480 Harbor Ave #210 Bayview, FL 33000</li>
    </ul>
    <div class="back-rule"></div>
  </section>
</body>
</html>
```